Business card for Luxury Portable Restroom Trailer company

We are a Luxury Portable Restroom Trailer Company Called FALCRIDGE HIRES. Based in Orange County California. We provide portable restroom trailers for events, such as, Weddings, Concerts, Charity events, Sporting events, Tournaments, Corporate events, ect. We rent and Sell the Luxury restrooms. Our colors are white, grey, and Orange. As you will see in the logo we uploaded.
There are 2 people in the company so the names and titles will change for the 3 people but card will remain the same. Here is the information for each Person: Dwight Penner CFO 555 318-0476
next Person: Leon Marchetti VP 555 318-0476
Next Person: Owen Marchetti CEO 555 318-0476
Information to include on the card: Luxury Restroom Trailers Rental and Sales. Weddings, Concerts, Charity, Sporting and Corp. Events.

```html
<!DOCTYPE html>
<html lang="en">
<head>
<meta charset="utf-8">
<title>Falcridge Hires – Business Card</title>
<link rel="stylesheet" href="https://fonts.googleapis.com/css2?family=Montserrat:wght@500;600;800&display=swap">
<style>
  :root {
    --orange: #f26f21;
    --grey: #58595b;
    --ink: #1f1f1f;
    --paper: #ffffff;
    --backdrop: #2a2a2a;
  }
  * { box-sizing: border-box; margin: 0; padding: 0; }
  html, body { width: 1200px; height: 880px; overflow: hidden; }
  body {
    background: var(--backdrop);
    font-family: "Montserrat", sans-serif;
    color: var(--ink);
    position: relative;
  }
  .card {
    position: absolute;
    left: 320px;
    width: 560px;
    height: 320px;
    background: var(--paper);
    overflow: hidden;
  }
  .card--front { top: 60px; }
  .card--back { top: 460px; }

  .brand-name {
    font-family: "Montserrat", sans-serif;
    font-weight: 800;
    color: var(--grey);
    letter-spacing: 0.04em;
    line-height: 1;
    white-space: nowrap;
  }

  /* front */
  .card--front .brand-name {
    position: absolute;
    top: 92px;
    left: 0;
    width: 100%;
    text-align: center;
    font-size: 40px;
  }
  .services {
    position: absolute;
    top: 180px;
    left: 0;
    width: 100%;
    text-align: center;
    font-weight: 500;
    font-size: 15px;
    line-height: 1.7;
  }
  .services li { list-style: none; }
  .services .item { white-space: nowrap; }
  .services .item::before {
    content: "";
    display: inline-block;
    width: 8px; height: 8px;
    border-radius: 50%;
    background: var(--orange);
    margin: 0 7px 1px 10px;
    vertical-align: middle;
  }

  /* back */
  .card--back .brand-name {
    position: absolute;
    top: 34px;
    right: 70px;
    font-size: 24px;
  }
  .wave { position: absolute; inset: 0; }
  .team {
    position: absolute;
    top: 84px;
    left: 40px;
    list-style: none;
  }
  .member { margin-bottom: 8px; }
  .member__name {
    font-weight: 800;
    font-size: 17px;
    color: var(--orange);
    text-transform: uppercase;
    letter-spacing: 0.02em;
    line-height: 1.15;
  }
  .member__title { font-size: 13px; font-weight: 500; line-height: 1.3; }
  .member__phone {
    font-size: 13px;
    font-weight: 500;
    display: flex;
    align-items: center;
    gap: 6px;
    line-height: 1.3;
  }
  .member__phone svg { width: 13px; height: 13px; fill: var(--orange); }
</style>
</head>
<body>

<section class="card card--front">
  <div class="brand-name">FALCRIDGE HIRES</div>
  <ul class="services">
    <li><span class="item">Luxury Restroom Trailers Rental and Sales</span></li>
    <li><span class="item">Weddings</span><span class="item">Concerts</span><span class="item">Charity</span><span class="item">Sporting and Corp</span><span class="item">Events</span></li>
  </ul>
</section>

<section class="card card--back">
  <svg class="wave" viewBox="0 0 560 320" width="560" height="320" aria-hidden="true">
    <path d="M0 300 C170 294 260 268 335 212 C400 164 455 146 560 134 L560 320 L0 320 Z" fill="var(--orange)"/>
    <path d="M0 288 C160 284 250 258 322 204 C360 176 385 166 416 160" fill="none" stroke="var(--grey)" stroke-width="9"/>
    <circle cx="470" cy="152" r="54" fill="var(--paper)" stroke="var(--orange)" stroke-width="6"/>
  </svg>

  <div class="brand-name">FALCRIDGE HIRES</div>

  <ul class="team">
    <li class="member">
      <div class="member__name">Dwight Penner</div>
      <div class="member__title">CFO</div>
      <div class="member__phone"><svg viewBox="0 0 24 24" aria-hidden="true"><path d="M6.6 10.8a15.1 15.1 0 0 0 6.6 6.6l2.2-2.2c.3-.3.7-.4 1-.2 1.1.4 2.3.6 3.6.6.6 0 1 .4 1 1V20c0 .6-.4 1-1 1A17 17 0 0 1 3 4c0-.6.4-1 1-1h3.5c.6 0 1 .4 1 1 0 1.3.2 2.5.6 3.6.1.3 0 .7-.2 1z"/></svg>555 318-0476</div>
    </li>
    <li class="member">
      <div class="member__name">Leon Marchetti</div>
      <div class="member__title">VP</div>
      <div class="member__phone"><svg viewBox="0 0 24 24" aria-hidden="true"><path d="M6.6 10.8a15.1 15.1 0 0 0 6.6 6.6l2.2-2.2c.3-.3.7-.4 1-.2 1.1.4 2.3.6 3.6.6.6 0 1 .4 1 1V20c0 .6-.4 1-1 1A17 17 0 0 1 3 4c0-.6.4-1 1-1h3.5c.6 0 1 .4 1 1 0 1.3.2 2.5.6 3.6.1.3 0 .7-.2 1z"/></svg>555 318-0476</div>
    </li>
    <li class="member">
      <div class="member__name">Owen Marchetti</div>
      <div class="member__title">CEO</div>
      <div class="member__phone"><svg viewBox="0 0 24 24" aria-hidden="true"><path d="M6.6 10.8a15.1 15.1 0 0 0 6.6 6.6l2.2-2.2c.3-.3.7-.4 1-.2 1.1.4 2.3.6 3.6.6.6 0 1 .4 1 1V20c0 .6-.4 1-1 1A17 17 0 0 1 3 4c0-.6.4-1 1-1h3.5c.6 0 1 .4 1 1 0 1.3.2 2.5.6 3.6.1.3 0 .7-.2 1z"/></svg>555 318-0476</div>
    </li>
  </ul>
</section>

</body>
</html>
```